Business Card design for law firm = Brightvale Australia

We are seeking a new design for our business cards.
We are keeping our logo, which is attached.
We need space for
Name
Title
Address is , which is
Level 7
214 Marlowe Street
Sydney NSW 2047
Phone :
Mobile :
Fax :
Email :
DX :
website www.brightvale-example.com.au

Industry/Entity Type

Law Firm / Banking and Finance

Contact Information for Business Card

We are seeking a new design for our business cards. We are keeping our logo. We need space for Name Title Address is Level 7 214 Marlowe Street Sydney NSW 2047 Phone Mobile Fax Email DX website www.brightvale-example.com.au

Colors
0054AA
0677BA
7BADD7
CADEEF
E8F1F8

Requirements
Must have
• see our website for general feel www.brightvale-example.com.au

```html
<!DOCTYPE html>
<html lang="en">
<head>
<meta charset="utf-8">
<title>Brightvale Australia – Business Card</title>
<link rel="stylesheet" href="https://fonts.googleapis.com/css2?family=Open+Sans:wght@400;700&family=Tinos&display=swap">
<style>
  :root {
    --stage: #2b2b2b;
    --card-dark: #0a0a0a;
    --card-light: #ffffff;
    --blue-deep: #0677BA;
    --blue-soft: #7BADD7;
    --ink: #1a1a1a;
  }
  * { margin: 0; padding: 0; box-sizing: border-box; }
  html, body { width: 1200px; height: 1015px; overflow: hidden; }
  body {
    background: var(--stage);
    position: relative;
    font-family: "Open Sans", sans-serif;
  }
  .card {
    position: absolute;
    width: 620px;
    height: 354px;
    box-shadow: 0 14px 30px rgba(0,0,0,.55);
  }
  .card--front { left: 80px; top: 90px; background: var(--card-dark); }
  .card--back  { left: 500px; top: 560px; background: var(--card-light); }

  /* Front: company name */
  .company {
    position: absolute;
    left: 0; right: 0; top: 132px;
    display: flex;
    flex-direction: column;
    align-items: center;
  }
  .company__name {
    font-size: 52px;
    font-weight: 400;
    line-height: 1;
    color: var(--blue-deep);
  }
  .company__tagline {
    margin-top: 14px;
    font-size: 16px;
    letter-spacing: 3px;
    color: var(--blue-soft);
  }

  /* Back: contact details */
  .person {
    position: absolute;
    left: 60px; top: 32px;
  }
  .person__name {
    font-family: "Tinos", serif;
    font-size: 30px;
    line-height: 1.1;
    color: var(--blue-deep);
  }
  .person__title { font-size: 15px; color: var(--ink); line-height: 1.3; }
  .contact {
    position: absolute;
    left: 78px; top: 104px;
    list-style: none;
    font-size: 15px;
    line-height: 1.45;
    color: var(--ink);
  }
  .contact__label { font-weight: 700; color: var(--blue-deep); }
  .contact__web-name { color: var(--blue-deep); }
  .address {
    position: absolute;
    left: 78px; bottom: 30px;
    font-style: normal;
    font-size: 15px;
    line-height: 1.35;
    color: var(--ink);
  }
</style>
</head>
<body>
  <section class="card card--front" aria-label="Card front">
    <div class="company">
      <span class="company__name">Brightvale</span>
      <span class="company__tagline">practical legal support</span>
    </div>
  </section>

  <section class="card card--back" aria-label="Card back">
    <div class="person">
      <div class="person__name">Daniel Hartley</div>
      <div class="person__title">Managing Director</div>
    </div>
    <ul class="contact">
      <li><span class="contact__label">P:</span> 044-555 010 200</li>
      <li><span class="contact__label">M:</span> 044-555 010 201</li>
      <li><span class="contact__label">F:</span> 044-555 010 202</li>
      <li><span class="contact__label">E:</span> info@brightvale-example.com.au</li>
      <li><span class="contact__label">DX:</span> 0000555010203</li>
      <li>www.<span class="contact__web-name">brightvale-example</span>.com.au</li>
    </ul>
    <address class="address">
      Level 7, 214 Marlowe Street<br>
      Sydney NSW 2047
    </address>
  </section>
</body>
</html>
```